Nanny Share Ecommerce Website for Finding Childcare and Parents who need Childcare BrightPramHub.net

Our company needs an ecommerce website (BrightPramHub.net) for a US subscription based service strictly for nanny sharing that connects families and caregivers. The website would allow families to connect with one another as well as to search for nannies. The service would be searchable for other families by location (by radius or zip code), children demographic (age range/gender/special needs), days of week or times, after school care, school closure days (holidays), etc. The service would also be searchable for nannies based on gender, provider age range, years experience, language, hourly rate, transportation available, certification (CPR first aid), education etc. The search fields would be searchable and sortable and allow to connect with the provider (after paying subscription fee). The service would be similar to tendlyfolk.net in that it would allow for families and caregivers to post photos as well as a short bio of the themselves. There would also be a feedback/star rating mechanism to rate caregivers who have performed work for families (viewable to public). The service would be free for nannies to post their bios and only a subscription based service for families to connect with other families or with caregivers (able to view bio but need service to connect). There will be a short bio on the benefits of nanny sharing (reduced cost, increased flexibility for parents, reduced illness, increased socialization with other children vs. sole nanny), as well as Q&A section with best practices.

Target Market(s)

Families, Nannies

Industry/Entity Type

Childcare

Logo Text

Bright Pram Hub

Coding

Coded - Design and coding required

Number of Pages Required

5+ page

Requirements
Must have
• Searchable (need to be able to search for families as well as nannies), responsive, functional, easy to use, add value to families and nannies. Needs to be able to collect payment for subscription.
Nice to have
• Optimized for mobile, SEO optimized

```html
<!DOCTYPE html>
<html lang="en">
<head>
<meta charset="utf-8">
<title>Bright Pram Hub — Connects families and Caregivers</title>
<link rel="stylesheet" href="https://fonts.googleapis.com/css2?family=Fredoka:wght@500;600&family=Open+Sans:wght@400;600;700&display=swap">
<style>
:root{
  --cyan:#1fc1ea;
  --pink:#f4628f;
  --ink:#222;
  --text:#555;
  --muted:#888;
  --line:#e3e3e3;
  --footer:#2a2a2a;
  --heading:'Fredoka',sans-serif;
  --body:'Open Sans',sans-serif;
}
*{box-sizing:border-box;margin:0;padding:0}
html,body{width:1200px;height:3448px;overflow:hidden}
body{position:relative;font-family:var(--body);color:var(--text);background:#fff}
section,header,footer{position:absolute;left:0;width:1200px;overflow:hidden}
.abs{position:absolute}
.center{text-align:center}
.section-title{position:absolute;left:0;width:1200px;text-align:center;font-family:var(--heading);font-weight:600;font-size:42px;color:var(--ink)}
.section-title span{position:relative;padding:0 40px}
.section-title span::before,.section-title span::after{content:"";position:absolute;top:50%;width:100px;height:1px;background:var(--line)}
.section-title span::before{right:100%}
.section-title span::after{left:100%}
.on-color .section-title{color:#fff}
.on-color .section-title span::before,.on-color .section-title span::after{background:rgba(255,255,255,.5)}

/* header */
.site-header{top:0;height:104px;border-top:5px solid var(--cyan);background:#fff}
.brand{left:100px;top:28px;display:flex;align-items:center;gap:12px;font-family:var(--heading);font-weight:600;font-size:27px;color:var(--ink)}
.brand i{width:34px;height:34px;border-radius:50%;border:3px solid var(--cyan);display:block}
.main-nav a{position:absolute;top:42px;font-size:14px;color:#444;text-decoration:none}
.main-nav a.active{color:var(--cyan)}
.search-icon{left:1088px;top:42px}

/* hero */
.hero{top:104px;height:551px;background:linear-gradient(100deg,#d9cdbf 0%,#efe6dc 35%,#f4f1ec 60%,#e8e4df 100%)}
.hero-photo{left:0;top:0;width:1200px;height:551px}
.hero-box{left:683px;top:144px;width:530px;height:262px;background:rgba(255,255,255,.94);border:2px solid var(--cyan);border-right:none;padding:30px 0 0 0}
.hero-box h1{position:absolute;left:-11px;top:22px;font-family:var(--heading);font-weight:600;font-size:50px;line-height:56px;color:var(--ink)}
.hero-box p{position:absolute;left:-11px;top:140px;font-size:14px;color:var(--muted)}
.btn{position:absolute;display:flex;align-items:center;justify-content:center;border-radius:24px;font-size:14px;font-weight:600;text-transform:uppercase;letter-spacing:.3px}
.btn-cyan{background:var(--cyan);color:#fff}
.btn-pink-outline{border:2px solid var(--pink);color:var(--pink);background:#fff}
.btn-pink{background:var(--pink);color:#fff}
.btn-white-outline{border:2px solid #fff;color:#fff}
.slider-arrow{width:42px;height:42px;border-radius:50%;background:#fff;display:flex;align-items:center;justify-content:center;box-shadow:0 1px 4px rgba(0,0,0,.15)}

/* services */
.services{top:655px;height:479px;background:#fff}
.service{width:320px}
.service h3{font-size:20px;font-weight:600;color:var(--ink);line-height:28px;margin-bottom:8px}
.service p{font-size:14px;line-height:24px;color:var(--muted)}
.service-left{left:32px;top:200px;text-align:right}
.service-right{left:849px;top:200px}
.btn-small{height:32px;width:113px;font-size:12px;font-weight:400;border:1.5px solid var(--pink);color:var(--pink);border-radius:18px}
.photo-circle{width:204px;height:204px;border-radius:50%;border:6px solid #fff;box-shadow:0 0 0 1px #ddd,0 2px 8px rgba(0,0,0,.1)}
.badge-dot{width:50px;height:50px;border-radius:50%;background:#fff;border:3px solid var(--cyan)}

/* about */
.about{top:1134px;height:556px;background:linear-gradient(110deg,#b57fc2 0%,#e07aa7 30%,#9d95d8 60%,#39bfe9 100%)}
.about h2{left:200px;top:90px;font-family:var(--heading);font-weight:600;font-size:42px;color:#fff}
.about h4{left:99px;top:154px;font-size:21px;font-weight:600;color:#fff}
.about p{left:99px;top:194px;width:508px;font-size:13px;line-height:24px;color:rgba(255,255,255,.92)}
.about-photo{left:644px;top:113px;width:460px;height:335px;border:5px solid #fff;background:linear-gradient(135deg,#d8c6b5,#9b8a7a 60%,#6b5c50)}

/* faq */
.faq{top:1690px;height:582px;background:#fff}
.faq .section-title{top:80px}
.faq-list{left:161px;top:168px;width:876px}
.faq-item{height:44px;border:1px solid var(--line);margin-bottom:11px;display:flex;align-items:center;justify-content:space-between;padding:0 18px;font-size:14px;color:#555}
.faq-item b{color:var(--pink);font-weight:700;margin-right:6px}
.faq-item .plus{width:14px;height:14px;border-radius:50%;background:#999;color:#fff;font-size:12px;line-height:14px;text-align:center}
.faq-item.open{background:var(--pink);color:#fff;border-color:var(--pink);margin-bottom:0}
.faq-item.open b{color:#fff}
.faq-item.open .plus{background:#fff;color:var(--pink)}
.faq-answer{border:1px solid var(--line);border-top:none;padding:14px 18px;font-size:13px;line-height:24px;color:var(--muted);margin-bottom:11px}

/* how it works */
.how{top:2272px;height:412px;background:linear-gradient(110deg,#e66c9c 0%,#b98bc8 40%,#56b8e8 75%,#22bfea 100%)}
.how .section-title{top:86px}
.step{width:200px;text-align:center}
.step .ring{width:104px;height:104px;margin:0 auto;border-radius:50%;background:#fff;border:5px solid rgba(255,255,255,.5);background-clip:padding-box;display:flex;align-items:center;justify-content:center}
.step span{display:block;margin-top:20px;color:#fff;font-size:20px;font-weight:600}
.step-line{top:226px;height:0;border-top:2px dotted rgba(255,255,255,.8)}

/* benefits */
.benefits{top:2684px;height:513px;background:#fff}
.benefits .section-title{top:78px}
.benefit{width:300px;text-align:center}
.benefit h3{margin-top:10px;font-size:17px;font-weight:600;color:#333}
.benefit p{margin-top:8px;font-size:13px;line-height:22px;color:var(--muted)}
.benefit .chev{margin-top:8px;color:var(--pink);font-size:14px}
.divider{top:260px;width:1px;height:110px;background:var(--line)}

/* footer */
.site-footer{top:3197px;height:251px;background:var(--footer);border-top:5px solid var(--cyan)}
.social{left:0;width:1200px;top:63px;display:flex;justify-content:center;gap:10px}
.social i{display:block;width:40px;height:40px;border-radius:50%;border:2px solid #fff}
.footer-nav{left:0;width:1200px;top:128px;text-align:center;font-size:14px;color:#fff}
.footer-nav em{font-style:normal;margin:0 14px;color:#ccc}
.copyright{left:0;width:1200px;top:172px;text-align:center;font-size:12px;color:#ddd}
</style>
</head>
<body>

<header class="site-header">
  <div class="abs brand"><i></i>Bright Pram Hub</div>
  <nav class="main-nav">
    <a class="active" style="left:480px">Home</a>
    <a style="left:570px">About us</a>
    <a style="left:675px">Services</a>
    <a style="left:778px">Feedbacks</a>
    <a style="left:895px">FAQ</a>
    <a style="left:972px">Contact us</a>
  </nav>
  <svg class="abs search-icon" width="16" height="16" viewBox="0 0 16 16"><circle cx="6.5" cy="6.5" r="4.5" fill="none" stroke="#f4628f" stroke-width="2"/><line x1="10" y1="10" x2="14" y2="14" stroke="#f4628f" stroke-width="2"/></svg>
</header>

<section class="hero">
  <div class="abs hero-photo" role="img" aria-label="Photo of a mother and young daughter stacking colourful toy blocks at a table" style="background:linear-gradient(100deg,#cbb9a6 0%,#e8d6c6 30%,#f3ece4 55%,#ece8e2 100%)"></div>
  <div class="abs hero-box">
    <h1>Connects families<br>and Caregivers</h1>
    <p>Sed ut perspiciatis unde omnis iste natus error sit voluptatem</p>
    <div class="btn btn-cyan" style="left:-11px;top:196px;width:144px;height:40px">Find care</div>
    <div class="btn btn-pink-outline" style="left:145px;top:196px;width:221px;height:40px">Search for nannies</div>
  </div>
  <div class="abs slider-arrow" style="left:20px;top:255px"><svg width="10" height="14"><path d="M8 1 2 7l6 6" fill="none" stroke="#555" stroke-width="2"/></svg></div>
  <div class="abs slider-arrow" style="left:1138px;top:255px"><svg width="10" height="14"><path d="m2 1 6 6-6 6" fill="none" stroke="#555" stroke-width="2"/></svg></div>
</section>

<section class="services">
  <h2 class="section-title" style="top:80px"><span>Our Services</span></h2>
  <div class="abs service service-left">
    <h3>Matching families</h3>
    <p>Sed ut perspiciatis unde omnis iste natus error sit voluptatem accusantium doloremque laudantium aae</p>
    <div class="btn btn-small" style="position:relative;margin:14px 0 0 auto">Read more</div>
  </div>
  <div class="abs photo-circle" role="img" aria-label="Photo of a smiling family of three" style="left:370px;top:180px;background:linear-gradient(135deg,#a98c72,#d8b99c 50%,#6f8aa3)"></div>
  <div class="abs photo-circle" role="img" aria-label="Photo of a family playing together on the floor" style="left:618px;top:180px;background:linear-gradient(135deg,#c9b29a,#e6dacb 50%,#9a7c63)"></div>
  <div class="abs badge-dot" style="left:568px;top:257px"></div>
  <div class="abs service service-right">
    <h3>Helping connect families<br>to nannies</h3>
    <p>Sed ut perspiciatis unde omnis iste natus error sit voluptatem accusantium</p>
    <div class="btn btn-small" style="position:relative;margin-top:14px">Read more</div>
  </div>
</section>

<section class="about">
  <h2 class="abs">About Us</h2>
  <h4 class="abs">We are more than just an nanny agency</h4>
  <p class="abs">At vero eos et accusamus et iusto odio dignissimos ducimus qui blanditiis praesentium voluptatum deleniti atque corrupti quos dolores et quas molestias excepturi sint occaecati cupiditate non provident, similique sunt in culpa qui officia deserunt mollitia animi, id est laborum et dolorum fuga. Et harum quidem rerum facilis est et expedita distinctio. Nam libero tempore.<br>Et harum quidem rerum facilis est et expedita distinctio. Nam libero tempore, cum soluta nobis est eligendi optio cumque nihil impedit quod maxime.</p>
  <div class="btn btn-white-outline" style="left:99px;top:412px;width:146px;height:46px">Read more</div>
  <div class="abs about-photo" role="img" aria-label="Photo of a mother and daughter playing on the floor with a small dog"></div>
</section>

<section class="faq">
  <h2 class="section-title"><span>Frequently asked Questions</span></h2>
  <div class="abs faq-list">
    <div class="faq-item open"><div><b>Q :</b>How do placeat facere possimus, omnis voluptas assumen?</div><div class="plus">–</div></div>
    <div class="faq-answer">Nam libero tempore, cum soluta nobis est eligendi optio cumque nihil impedit qenetur a sapiente delectus minus id quod maxime placeat facere possimusetur a sapiente delect..</div>
    <div class="faq-item"><div><b>Q .</b>If erum facilis est et expedita distin?</div><div class="plus">+</div></div>
    <div class="faq-item"><div><b>Q .</b>If ero eos et accusamus et iusto odio?</div><div class="plus">+</div></div>
    <div class="faq-item"><div><b>Q .</b>Where again is there anyone who loves?</div><div class="plus">+</div></div>
    <div class="faq-item"><div><b>Q .</b>Why facilis est et expedita distin?</div><div class="plus">+</div></div>
  </div>
</section>

<section class="how on-color">
  <h2 class="section-title"><span>How it Works</span></h2>
  <div class="abs step-line" style="left:215px;width:770px"></div>
  <div class="abs step" style="left:61px;top:174px"><div class="ring"><svg width="40" height="40" viewBox="0 0 40 40"><rect x="6" y="8" width="24" height="24" rx="3" fill="none" stroke="#1fc1ea" stroke-width="3"/><path d="M16 24l2-6 14-14 4 4-14 14z" fill="#1fc1ea"/></svg></div><span>Sign up</span></div>
  <div class="abs step" style="left:275px;top:174px"><div class="ring"><svg width="40" height="40" viewBox="0 0 40 40"><path d="M10 4h14l8 8v24H10z" fill="none" stroke="#1fc1ea" stroke-width="3"/><path d="M15 18h12M15 24h12M15 30h8" stroke="#1fc1ea" stroke-width="3"/></svg></div><span>Create a job</span></div>
  <div class="abs step" style="left:484px;top:174px"><div class="ring"><svg width="40" height="40" viewBox="0 0 40 40"><path d="M20 3l5 11 12 1-9 8 3 12-11-6-11 6 3-12-9-8 12-1z" fill="#1fc1ea"/></svg></div><span>Review profiles</span></div>
  <div class="abs step" style="left:700px;top:174px"><div class="ring"><svg width="40" height="40" viewBox="0 0 40 40"><path d="M6 18h7v18H6zM15 18l6-12c3 0 4 2 3 5l-1 6h10c2 0 3 2 3 4l-3 12c-1 2-2 3-4 3H15z" fill="none" stroke="#1fc1ea" stroke-width="3" stroke-linejoin="round"/></svg></div><span>Hire a caregiver</span></div>
  <div class="abs step" style="left:912px;top:174px"><div class="ring"><svg width="40" height="40" viewBox="0 0 40 40"><text x="20" y="31" text-anchor="middle" font-family="Open Sans,sans-serif" font-size="30" font-weight="700" fill="#1fc1ea">$</text></svg></div><span>Pay for your care</span></div>
</section>

<section class="benefits">
  <h2 class="section-title"><span>Our benefits</span></h2>
  <div class="abs benefit" style="left:73px;top:160px">
    <svg width="40" height="50" viewBox="0 0 40 50"><path d="M20 4v42M28 14c-2-4-14-5-15 2s15 6 15 14-14 8-16 2" fill="none" stroke="#1fc1ea" stroke-width="2.5"/></svg>
    <h3>Reduced cost</h3>
    <p>Nam libero tempore cum soluta nobis est eligendi optio cumque nihil impedit quo minus id quod maxime placeat</p>
    <div class="chev">&#8744;</div>
  </div>
  <div class="abs divider" style="left:410px"></div>
  <div class="abs benefit" style="left:450px;top:160px">
    <svg width="60" height="50" viewBox="0 0 60 50"><circle cx="18" cy="10" r="5" fill="none" stroke="#1fc1ea" stroke-width="2.5"/><circle cx="42" cy="10" r="5" fill="none" stroke="#1fc1ea" stroke-width="2.5"/><circle cx="30" cy="26" r="4" fill="none" stroke="#1fc1ea" stroke-width="2.5"/><path d="M10 46V22h16v24M34 46V22h16v24M25 46V34h10v12" fill="none" stroke="#1fc1ea" stroke-width="2.5"/></svg>
    <h3>Increased flexibility for parents</h3>
    <p>Nam libero tempore cum soluta nobis est eligendi optio cumque nihil impedit quo minus id quod maxime placeat</p>
    <div class="chev">&#8744;</div>
  </div>
  <div class="abs divider" style="left:790px"></div>
  <div class="abs benefit" style="left:825px;top:160px">
    <svg width="50" height="50" viewBox="0 0 50 50"><circle cx="25" cy="12" r="7" fill="none" stroke="#1fc1ea" stroke-width="2.5"/><path d="M8 46c0-14 8-22 17-22s17 8 17 22" fill="none" stroke="#1fc1ea" stroke-width="2.5"/><path d="M18 36h14M25 29v14" stroke="#1fc1ea" stroke-width="2.5"/></svg>
    <h3>Reduced illness</h3>
    <p>Nam libero tempore cum soluta nobis est eligendi optio cumque nihil impedit quo minus id quod maxime placeat</p>
    <div class="chev">&#8744;</div>
  </div>
  <svg class="abs" style="left:56px;top:280px" width="12" height="18"><path d="M10 2 3 9l7 7" fill="none" stroke="#333" stroke-width="2.5"/></svg>
  <svg class="abs" style="left:1130px;top:280px" width="12" height="18"><path d="m2 2 7 7-7 7" fill="none" stroke="#333" stroke-width="2.5"/></svg>
  <div class="btn btn-pink" style="left:529px;top:382px;width:146px;height:40px">View more</div>
</section>

<footer class="site-footer">
  <div class="abs social"><i></i><i></i><i></i><i></i><i></i><i></i><i></i></div>
  <div class="abs footer-nav">Home<em>/</em>About us<em>/</em>Services<em>/</em>How it works<em>/</em>FAQ<em>/</em>Contact us</div>
  <div class="abs copyright">© Copyright 2018 Bright Pram Hub.All Rights Reserved</div>
</footer>

</body>
</html>
```